Need help in designing new business card utilizing our new logo.

BuildMark Solutions works with Construction Business Owners, Managers & IT Professionals to strengthen software usage and increase user productivity.

Our Construction Accounting and Mobile Field Management Software Clients engage with us in the following areas:

New Software Implementations
Software Re-Implementations
Redesigning Software Usage at the User Level
Project Coordination & Management
Continued Software Support

Old tag line:
Weighing Options - Implementing Solutions

www.buildmark-solutions.example

Ridge 4 is a product, but not needed for a new business card.

```html
<!DOCTYPE html>
<html lang="en">
<head>
<meta charset="utf-8">
<title>BuildMark Solutions – Business Card</title>
<link rel="stylesheet" href="https://fonts.googleapis.com/css2?family=Open+Sans:wght@400;600;700&display=swap">
<style>
  :root {
    --brand-blue: #1f2fb8;
    --deep-blue: #0a16a6;
    --band-blue: #2b3bc4;
    --band-shade: #1626ad;
    --ink-grey: #4a4a4a;
    --soft-grey: #b9bcc4;
    --rule-grey: #c9cbd2;
    --paper: #ffffff;
    --backdrop: #e9e9ec;
  }
  * { box-sizing: border-box; margin: 0; padding: 0; }
  html, body {
    width: 1200px; height: 950px; overflow: hidden;
    background: var(--backdrop);
    font-family: "Open Sans", Arial, sans-serif;
  }
  .canvas { position: relative; width: 1200px; height: 950px; }
  .card {
    position: absolute; left: 250px; width: 700px; height: 400px;
    overflow: hidden; box-shadow: 0 6px 18px rgba(0,0,0,0.15);
  }

  /* Front */
  .card-front { top: 55px; background: var(--paper); }
  .front-band { position: absolute; left: 0; bottom: 0; width: 700px; height: 120px; }
  .band-label {
    position: absolute; left: 40px; bottom: 26px;
    color: var(--paper); font-size: 21px; font-weight: 600; letter-spacing: 0.3px;
    white-space: nowrap;
  }
  .brand-block {
    position: absolute; left: 40px; top: 112px;
    display: flex; align-items: center; gap: 12px;
  }
  .brand-square { width: 30px; height: 30px; background: var(--brand-blue); flex: none; }
  .brand-name { color: var(--brand-blue); font-size: 24px; font-weight: 600; white-space: nowrap; }
  .vertical-rule {
    position: absolute; left: 345px; top: 24px; width: 1px; height: 240px;
    background: linear-gradient(to bottom, rgba(201,203,210,0), var(--rule-grey) 30%, var(--rule-grey) 70%, rgba(201,203,210,0));
  }
  .contact-block { position: absolute; left: 368px; top: 30px; color: var(--ink-grey); }
  .person-name { color: var(--brand-blue); font-size: 21px; font-weight: 700; letter-spacing: 0.5px; white-space: nowrap; }
  .person-role { color: var(--soft-grey); font-size: 14px; font-weight: 700; margin-bottom: 20px; }
  .address-line { font-size: 14px; line-height: 22px; white-space: nowrap; }
  .contact-list { list-style: none; margin-top: 4px; }
  .contact-list li {
    display: flex; align-items: center; gap: 8px;
    font-size: 13.5px; line-height: 22px; white-space: nowrap;
  }
  .contact-list svg { width: 12px; height: 12px; fill: var(--brand-blue); flex: none; }

  /* Back */
  .card-back { top: 495px; background: var(--deep-blue); color: var(--paper); }
  .back-brand {
    position: absolute; left: 0; right: 0; top: 60px;
    display: flex; justify-content: center; align-items: center; gap: 16px;
  }
  .back-brand .brand-square { background: var(--paper); width: 40px; height: 40px; }
  .back-brand .brand-name { color: var(--paper); font-size: 30px; }
  .services { position: absolute; left: 40px; right: 40px; top: 175px; }
  .services-heading { font-size: 16px; font-weight: 700; line-height: 22px; text-transform: uppercase; margin-bottom: 10px; }
  .service-line { font-size: 16px; line-height: 24px; white-space: nowrap; }
  .tagline { margin-top: 10px; font-size: 16px; letter-spacing: 0.4px; }
</style>
</head>
<body>
<main class="canvas">

  <section class="card card-front" aria-label="Card front">
    <div class="brand-block">
      <span class="brand-square"></span>
      <span class="brand-name">BuildMark Solutions</span>
    </div>

    <div class="vertical-rule" aria-hidden="true"></div>

    <div class="contact-block">
      <p class="person-name">DANA R. HOLLIS</p>
      <p class="person-role">OWNER</p>
      <p class="address-line">14 linden avenue-suite 210</p>
      <p class="address-line">glenmore falls NY 10000</p>
      <ul class="contact-list">
        <li><svg viewBox="0 0 16 16"><path d="M3 1l3 3-2 2c1 2 3 4 5 5l2-2 3 3-2 3C7 15 1 9 1 3z"/></svg>800-555-0142 ext.100</li>
        <li><svg viewBox="0 0 16 16"><rect x="4" y="1" width="8" height="14" rx="1.5"/></svg>518-555-0187</li>
        <li><svg viewBox="0 0 16 16"><path d="M1 3h14v10H1z M1 3l7 6 7-6"/></svg>dana.hollis@buildmark-solutions.example</li>
        <li><svg viewBox="0 0 16 16"><circle cx="8" cy="8" r="7"/></svg>www.buildmark-solutions.example</li>
      </ul>
    </div>

    <svg class="front-band" viewBox="0 0 700 120" aria-hidden="true">
      <polygon points="0,40 640,40 700,0 700,120 0,120" fill="var(--band-blue)"/>
      <polygon points="560,40 640,40 700,0 700,20 660,40" fill="var(--band-shade)"/>
    </svg>
    <p class="band-label">CONSTRUCTION ACCOUNTING SOFTWARE CONSULTANTS</p>
  </section>

  <section class="card card-back" aria-label="Card back">
    <div class="back-brand">
      <span class="brand-square"></span>
      <span class="brand-name">BuildMark Solutions</span>
    </div>
    <div class="services">
      <p class="services-heading">Construction accounting and mobile field management software clients engage with us in the following areas:</p>
      <p class="service-line">New Software Implementations • Software Re-Implementations</p>
      <p class="service-line">Redesigning Software Usage at the User Level</p>
      <p class="service-line">Project Coordination &amp; Management • Continued Software Support</p>
      <p class="tagline">WEIGHING OPTIONS - IMPLEMENTING SOLUTIONS</p>
    </div>
  </section>

</main>
</body>
</html>
```